New National Dermatology Group needs a business card!

We need a business card for our new national company that has 3 brands within the business:
Lumora Clinics Australia, Tessaly Clinics Australia and Corvane Clinics Australia.
We help people access dermatology services close to home throughout Australia.
We need a business card that has:
all 3 logos on it,
Our websites (there are three, listed above)
Our email (there are three, listed above)
The location of our first clinic: 41 Willow Rd Parramatta (this can then be changed for each location as required)

```html
<!DOCTYPE html>
<html lang="en">
<head>
<meta charset="utf-8">
<title>Corvane, Lumora and Tessaly Clinics Australia – Business Card</title>
<link rel="stylesheet" href="https://fonts.googleapis.com/css2?family=Open+Sans:wght@400;600&display=swap">
<style>
  :root {
    --bg: #1b1b1b;
    --card: #121212;
    --brown: #7d3e1c;
    --green: #1fae4b;
    --orange: #f58220;
    --ink: #f2f2f2;
    --card-w: 620px;
    --card-h: 354px;
  }
  * { box-sizing: border-box; margin: 0; padding: 0; }
  html, body {
    width: 1200px; height: 900px; overflow: hidden;
    background: var(--bg);
    font-family: "Open Sans", Arial, sans-serif;
  }
  .stage {
    width: 1200px; height: 900px;
    display: flex; flex-direction: column; align-items: center; justify-content: center;
    gap: 40px;
  }
  .card {
    position: relative;
    width: var(--card-w); height: var(--card-h);
    background: var(--card);
    box-shadow: 0 10px 30px rgba(0,0,0,.55);
    overflow: hidden;
  }
  .card-stripe {
    position: absolute; left: 0; right: 0; bottom: 0; height: 12px;
    display: flex;
  }
  .card-stripe span { flex: 1; }
  .stripe-brown { background: var(--brown); }
  .stripe-green { background: var(--green); }
  .stripe-orange { background: var(--orange); }

  .brand { font-weight: 600; line-height: 1; text-transform: uppercase; }
  .brand-name { display: block; letter-spacing: .08em; }
  .brand-sub { display: block; letter-spacing: .32em; margin-top: 4px; }
  .brand--brown { color: var(--brown); }
  .brand--green { color: var(--green); }
  .brand--orange { color: var(--orange); }

  /* Front */
  .front-brands {
    position: absolute; left: 170px; top: 48px;
    display: flex; flex-direction: column; gap: 20px;
  }
  .front-brands .brand-name { font-size: 42px; }
  .front-brands .brand-sub { font-size: 12px; }

  /* Back */
  .back-brands {
    position: absolute; left: 28px; right: 28px; top: 26px;
    display: flex; justify-content: space-between;
  }
  .back-brands .brand-name { font-size: 27px; }
  .back-brands .brand-sub { font-size: 8px; letter-spacing: .28em; }

  .contact-rows {
    position: absolute; left: 36px; right: 36px; top: 104px;
    display: flex; flex-direction: column; gap: 16px;
  }
  .contact-row {
    position: relative;
    display: flex; justify-content: space-between;
  }
  .contact-row::before {
    content: ""; position: absolute; left: 13px; right: 13px; top: 13px;
    height: 1px; background: var(--row-colour);
  }
  .contact-row--brown { --row-colour: var(--brown); }
  .contact-row--green { --row-colour: var(--green); }
  .contact-row--orange { --row-colour: var(--orange); }
  .contact-item {
    position: relative; width: 170px;
    display: flex; flex-direction: column; gap: 7px;
  }
  .contact-item:last-child { align-items: flex-end; }
  .contact-item:nth-child(2) { align-items: center; }
  .contact-icon {
    width: 27px; height: 27px; border-radius: 50%;
    border: 1.5px solid var(--row-colour); color: var(--row-colour);
    background: var(--card);
    display: flex; align-items: center; justify-content: center;
  }
  .contact-icon svg { width: 15px; height: 15px; }
  .contact-text { color: var(--ink); font-size: 15px; white-space: nowrap; }
</style>
</head>
<body>
<main class="stage">

  <section class="card card--front" aria-label="Card front">
    <div class="front-brands">
      <p class="brand brand--brown"><span class="brand-name">Corvane</span><span class="brand-sub">Clinics Australia</span></p>
      <p class="brand brand--green"><span class="brand-name">Lumora</span><span class="brand-sub">Clinics Australia</span></p>
      <p class="brand brand--orange"><span class="brand-name">Tessaly</span><span class="brand-sub">Clinics Australia</span></p>
    </div>
    <div class="card-stripe"><span class="stripe-brown"></span><span class="stripe-green"></span><span class="stripe-orange"></span></div>
  </section>

  <section class="card card--back" aria-label="Card back">
    <div class="back-brands">
      <p class="brand brand--brown"><span class="brand-name">Corvane</span><span class="brand-sub">Clinics Australia</span></p>
      <p class="brand brand--green"><span class="brand-name">Lumora</span><span class="brand-sub">Clinics Australia</span></p>
      <p class="brand brand--orange"><span class="brand-name">Tessaly</span><span class="brand-sub">Clinics Australia</span></p>
    </div>

    <div class="contact-rows">
      <div class="contact-row contact-row--brown">
        <div class="contact-item">
          <span class="contact-icon"><svg viewBox="0 0 16 16" fill="none" stroke="currentColor" stroke-width="1.4"><rect x="1.5" y="3.5" width="13" height="9"/><path d="M1.5 3.5 8 9l6.5-5.5"/></svg></span>
          <span class="contact-text">hello@clinicmail.com.au</span>
        </div>
        <div class="contact-item">
          <span class="contact-icon"><svg viewBox="0 0 16 16" fill="none" stroke="currentColor" stroke-width="1.2"><circle cx="8" cy="8" r="6.5"/><ellipse cx="8" cy="8" rx="3" ry="6.5"/><path d="M1.5 8h13M2.5 4.8h11M2.5 11.2h11"/></svg></span>
          <span class="contact-text">www.clinicsite.com.au</span>
        </div>
        <div class="contact-item">
          <span class="contact-icon"><svg viewBox="0 0 16 16" fill="currentColor"><path d="M8 1a5 5 0 0 0-5 5c0 3.6 5 9 5 9s5-5.4 5-9a5 5 0 0 0-5-5zm0 7a2 2 0 1 1 0-4 2 2 0 0 1 0 4z"/></svg></span>
          <span class="contact-text">41 Willow Rd Parramatta</span>
        </div>
      </div>

      <div class="contact-row contact-row--green">
        <div class="contact-item">
          <span class="contact-icon"><svg viewBox="0 0 16 16" fill="none" stroke="currentColor" stroke-width="1.4"><rect x="1.5" y="3.5" width="13" height="9"/><path d="M1.5 3.5 8 9l6.5-5.5"/></svg></span>
          <span class="contact-text">hello@clinicmail.com.au</span>
        </div>
        <div class="contact-item">
          <span class="contact-icon"><svg viewBox="0 0 16 16" fill="none" stroke="currentColor" stroke-width="1.2"><circle cx="8" cy="8" r="6.5"/><ellipse cx="8" cy="8" rx="3" ry="6.5"/><path d="M1.5 8h13M2.5 4.8h11M2.5 11.2h11"/></svg></span>
          <span class="contact-text">www.clinicsite.com.au</span>
        </div>
        <div class="contact-item">
          <span class="contact-icon"><svg viewBox="0 0 16 16" fill="currentColor"><path d="M8 1a5 5 0 0 0-5 5c0 3.6 5 9 5 9s5-5.4 5-9a5 5 0 0 0-5-5zm0 7a2 2 0 1 1 0-4 2 2 0 0 1 0 4z"/></svg></span>
          <span class="contact-text">41 Willow Rd Parramatta</span>
        </div>
      </div>

      <div class="contact-row contact-row--orange">
        <div class="contact-item">
          <span class="contact-icon"><svg viewBox="0 0 16 16" fill="none" stroke="currentColor" stroke-width="1.4"><rect x="1.5" y="3.5" width="13" height="9"/><path d="M1.5 3.5 8 9l6.5-5.5"/></svg></span>
          <span class="contact-text">hello@clinicmail.com.au</span>
        </div>
        <div class="contact-item">
          <span class="contact-icon"><svg viewBox="0 0 16 16" fill="none" stroke="currentColor" stroke-width="1.2"><circle cx="8" cy="8" r="6.5"/><ellipse cx="8" cy="8" rx="3" ry="6.5"/><path d="M1.5 8h13M2.5 4.8h11M2.5 11.2h11"/></svg></span>
          <span class="contact-text">www.clinicsite.com.au</span>
        </div>
        <div class="contact-item">
          <span class="contact-icon"><svg viewBox="0 0 16 16" fill="currentColor"><path d="M8 1a5 5 0 0 0-5 5c0 3.6 5 9 5 9s5-5.4 5-9a5 5 0 0 0-5-5zm0 7a2 2 0 1 1 0-4 2 2 0 0 1 0 4z"/></svg></span>
          <span class="contact-text">41 Willow Rd Parramatta</span>
        </div>
      </div>
    </div>

    <div class="card-stripe"><span class="stripe-brown"></span><span class="stripe-green"></span><span class="stripe-orange"></span></div>
  </section>

</main>
</body>
</html>
```